RiverPine - Rebranding, Namecard, Stationary and One Page Web

Refresh logo, make it modern and design matching name card, stationary and one page web

RiverPine Information Technology (Int'l) Company Limited
松河訊息科技(國際)有限公司

Company is System Integrator, and will be providing products and services to government and enterprise organizations. Our Chief Security Officer came from top U.S. vendor, and had been working on top enterprise and government projects globally, so we want the refreshed image of the new company to have a East Cost U.S. style, with hint of technology from Silicon Valley. The company will also be representing top brands from the U.S. on information security.

Branding refresh is needed because company is being acquired and is expanding

Target Market(s)

Cyber Security

Industry/Entity Type

Information Technology

Contact Information for Business Card

Need Chinese and English

Number of Pages Required

1 page

Font styles to use
Sans Serif

Colors
0292cd
00a990

Requirements
Must have
• Modern, clean, cyber look. Must keep same colors and general look and feel of original logo. Only modernization, do not change its personality

```html
<!DOCTYPE html>
<html lang="en">
<head>
<meta charset="utf-8">
<title>RiverPine Stationery Set</title>
<link href="https://fonts.googleapis.com/css2?family=Open+Sans:wght@400;600;700&family=Oswald:wght@400;500&family=Tinos&display=swap" rel="stylesheet">
<style>
  :root{
    --bg:#f1f2f3;
    --paper:#fbfbfb;
    --paper-edge:#e2e4e6;
    --brand-blue:#0292cd;
    --card-blue:#1b93d3;
    --brand-teal:#00a990;
    --logo-blue:#1f9ad6;
    --ink:#333a40;
    --grey:#8a8d90;
    --pen:#2aa2dc;
  }
  *{box-sizing:border-box;margin:0;padding:0}
  html,body{width:1200px;height:1000px;overflow:hidden;background:var(--bg)}
  body{position:relative;font-family:"Open Sans",Arial,sans-serif;color:var(--ink)}
  .piece{position:absolute;background:var(--paper);border:1px solid var(--paper-edge);overflow:hidden}
  .wordmark{position:absolute;font-family:"Open Sans",Arial,sans-serif;font-weight:700;color:var(--logo-blue);white-space:nowrap;display:flex;align-items:center;gap:6px}
  .wordmark .dot{display:inline-block;border-radius:50%;background:currentColor}

  /* notepad */
  .notepad{left:55px;top:115px;width:170px;height:240px}
  .notepad .rings{position:absolute;left:10px;top:0;width:150px;height:14px}
  .notepad .wordmark{left:50%;top:125px;transform:translateX(-50%);font-size:19px}

  /* dark business card */
  .card-front{left:25px;top:393px;width:265px;height:160px;background:var(--card-blue);border:none}
  .card-front .wordmark{color:#fff;left:50%;top:60px;transform:translateX(-50%);font-size:18px}
  .card-front .company{position:absolute;left:0;right:0;top:105px;text-align:center;color:#fff;font-size:6.3px;line-height:9px;font-weight:600}

  /* white business card */
  .card-back{left:25px;top:592px;width:265px;height:160px}
  .card-back .wordmark{right:20px;top:26px;font-size:16px}
  .card-back .name{position:absolute;left:14px;top:78px;font-size:11px;font-weight:700;color:var(--brand-blue)}
  .card-back .role{position:absolute;left:14px;top:92px;font-size:7.5px;color:var(--grey)}
  .card-back .rule{position:absolute;left:14px;top:103px;width:250px;border-top:1px solid #c9ccce}
  .card-back .contacts{position:absolute;left:14px;top:113px}
  .card-back .address{position:absolute;right:12px;top:113px;text-align:right;font-size:5.6px;line-height:8px;color:var(--ink)}
  .card-back .band{position:absolute;left:0;bottom:0;width:100%;height:14px}

  .contact-list{list-style:none;font-size:6px;line-height:9px;color:var(--ink)}
  .contact-list li{display:flex;align-items:center;gap:5px}
  .contact-list svg{width:6px;height:6px;flex:none}
  .contact-list .web b{color:var(--brand-blue);font-weight:400}

  /* letterhead */
  .letterhead{left:320px;top:97px;width:397px;height:560px}
  .letterhead .wordmark{left:40px;top:48px;font-size:21px}
  .letterhead .contacts{position:absolute;left:208px;top:58px}
  .letterhead .contacts .contact-list{font-size:8.5px;line-height:12.5px}
  .letterhead .contacts svg{width:7px;height:7px}
  .greeting{position:absolute;left:40px;top:143px;font-family:"Oswald",Arial,sans-serif;color:var(--grey);line-height:1}
  .greeting h1{font-size:27px;font-weight:400}
  .greeting p{font-size:12px;font-weight:500;margin-top:3px}
  .letter-date{position:absolute;right:44px;top:161px;font-size:8.5px;color:var(--ink)}
  .letter-body{position:absolute;left:40px;top:202px;width:318px;font-family:"Tinos",serif;font-size:6.3px;line-height:8.2px;color:#444}
  .letter-body p{margin-bottom:8px;text-align:justify}
  .letter-sign{font-family:"Tinos",serif}
  .letter-footer{position:absolute;left:38px;top:522px;display:flex;align-items:center;gap:6px;font-size:6.6px;line-height:9px}
  .letter-footer strong{color:var(--brand-blue);font-size:7.5px;font-weight:700;padding-right:5px;border-right:1px solid var(--brand-blue)}
  .letterhead .band{position:absolute;left:0;bottom:0;width:100%;height:18px}

  /* folder */
  .folder{left:740px;top:67px;width:435px;height:593px}
  .folder .flap{position:absolute;left:374px;top:0;width:1px;height:100%;background:var(--paper-edge)}
  .folder .wordmark{left:72px;top:276px;font-size:40px;gap:10px}

  /* pens */
  .pen{position:absolute;left:40px;width:242px;height:10px;border-radius:5px 2px 2px 5px;background:var(--pen)}
  .pen-one{top:823px}
  .pen-two{top:873px}

  /* envelope front */
  .envelope-front{left:320px;top:688px;width:417px;height:209px}
  .envelope-front .wordmark{left:24px;top:48px;font-size:16px}
  .envelope-front .contacts{position:absolute;left:22px;top:140px}
  .envelope-front .divider{position:absolute;left:157px;top:140px;height:28px;border-left:1px solid var(--brand-blue)}
  .envelope-front .address{position:absolute;left:176px;top:140px;font-size:6px;line-height:9.5px}
  .envelope-front .band{position:absolute;left:0;bottom:0;width:100%;height:16px}

  /* envelope back */
  .envelope-back{left:754px;top:685px;width:414px;height:207px}
  .envelope-back .fold{position:absolute;inset:0;width:100%;height:100%}
  .envelope-back .wordmark{left:50%;top:124px;transform:translateX(-50%);font-size:19px}
</style>
</head>
<body>

<!-- notepad -->
<section class="piece notepad" aria-label="Spiral notepad">
  <svg class="rings" viewBox="0 0 150 14" aria-hidden="true">
    <g fill="none" stroke="#b9bcbf" stroke-width="1.4">
      <circle cx="10" cy="6" r="4"/><circle cx="28" cy="6" r="4"/><circle cx="46" cy="6" r="4"/>
      <circle cx="64" cy="6" r="4"/><circle cx="82" cy="6" r="4"/><circle cx="100" cy="6" r="4"/>
      <circle cx="118" cy="6" r="4"/><circle cx="136" cy="6" r="4"/>
    </g>
  </svg>
  <div class="wordmark">RiverPine</div>
</section>

<!-- business card front -->
<section class="piece card-front" aria-label="Business card front">
  <div class="wordmark">RiverPine</div>
  <div class="company">
    RiverPine Information Technology (Int'l) Company Limited<br>
    松河訊息科技(國際)有限公司
  </div>
</section>

<!-- business card back -->
<section class="piece card-back" aria-label="Business card back">
  <div class="wordmark">RiverPine</div>
  <div class="name">DANIEL WONG</div>
  <div class="role">CEO</div>
  <div class="rule"></div>
  <div class="contacts">
    <ul class="contact-list">
      <li><svg viewBox="0 0 10 10"><path d="M2 1l2 2-1 1.5c.6 1.2 1.4 2 2.5 2.5L7 6l2 2-1.5 1.5C5 9 1 5 .5 2.5z" fill="#0292cd"/></svg>(852) 5512 0846</li>
      <li><svg viewBox="0 0 10 10"><rect x="0.5" y="2" width="9" height="6" fill="#0292cd"/><path d="M.5 2l4.5 3.5L9.5 2" stroke="#fff" fill="none" stroke-width=".8"/></svg>danielwong@hkriverpine.com.hk</li>
      <li class="web"><svg viewBox="0 0 10 10"><circle cx="5" cy="5" r="4.5" fill="#0292cd"/></svg>www.<b>hkriverpine</b>.com.hk</li>
    </ul>
  </div>
  <div class="address">Room C, Unit 408, 4/F, Lok Tin Ind. Bldg,<br>No. 12 Hoi Yuen Road, Kwun Tong,<br>Kowloon, HKSAR</div>
  <svg class="band" viewBox="0 0 265 14" preserveAspectRatio="none" aria-hidden="true">
    <rect x="0" y="9" width="265" height="5" fill="#0292cd"/>
    <path d="M180 9 L190 3 L265 3 L265 9 Z" fill="#0292cd"/>
  </svg>
</section>

<!-- letterhead -->
<section class="piece letterhead" aria-label="Letterhead">
  <div class="wordmark">RiverPine</div>
  <div class="contacts">
    <ul class="contact-list">
      <li><svg viewBox="0 0 10 10"><path d="M2 1l2 2-1 1.5c.6 1.2 1.4 2 2.5 2.5L7 6l2 2-1.5 1.5C5 9 1 5 .5 2.5z" fill="#0292cd"/></svg>(852) 5512 0846</li>
      <li><svg viewBox="0 0 10 10"><rect x="0.5" y="2" width="9" height="6" fill="#0292cd"/><path d="M.5 2l4.5 3.5L9.5 2" stroke="#fff" fill="none" stroke-width=".8"/></svg>danielwong@hkriverpine.com.hk</li>
      <li class="web"><svg viewBox="0 0 10 10"><circle cx="5" cy="5" r="4.5" fill="#0292cd"/></svg>www.<b>hkriverpine</b>.com.hk</li>
    </ul>
  </div>
  <div class="greeting">
    <h1>HELLO</h1>
    <p>MR. LEE</p>
  </div>
  <div class="letter-date">Date: 00 / 00 / 00</div>
  <div class="letter-body">
    <p>Lorem ipsum dolor sit amet, consectetuer adipiscing elit. Aenean commodo ligula eget dolor. Aenean massa. Cum sociis natoque penatibus et magnis dis parturient montes, nascetur ridiculus mus.</p>
    <p>Donec quam felis, ultricies nec, pellentesque eu, pretium quis, sem. Nulla consequat massa quis enim. Donec pede justo, fringilla vel, aliquet nec, vulputate eget, arcu. In enim justo, rhoncus ut, imperdiet a, venenatis vitae, justo. Nullam dictum felis eu pede mollis pretium. Integer tincidunt. Cras dapibus. Vivamus elementum semper nisi. Aenean vulputate eleifend tellus. Aenean leo ligula, porttitor eu, consequat vitae, eleifend ac, enim. Aliquam lorem ante, dapibus in, viverra quis, feugiat a, tellus. Phasellus viverra nulla ut metus varius laoreet. Quisque rutrum. Aenean imperdiet. Etiam ultricies nisi vel augue. Curabitur ullamcorper ultricies nisi. Nam eget dui.</p>
    <p>Etiam rhoncus. Maecenas tempus, tellus eget condimentum rhoncus, sem quam semper libero, sit amet adipiscing sem neque sed ipsum. Nam quam nunc, blandit vel, luctus pulvinar, hendrerit id, lorem. Maecenas nec odio et ante tincidunt tempus. Donec vitae sapien ut libero venenatis faucibus. Nullam quis ante.</p>
    <p>Etiam sit amet orci eget eros faucibus tincidunt. Duis leo. Sed fringilla mauris sit amet nibh. Donec sodales sagittis magna. Sed consequat, leo eget bibendum sodales, augue velit cursus nunc,</p>
    <p>Etiam rhoncus. Maecenas tempus, tellus eget condimentum rhoncus, sem quam semper libero, sit amet adipiscing sem neque sed ipsum. Nam quam nunc, blandit vel, luctus pulvinar, hendrerit id, lorem. Maecenas nec odio et ante tincidunt tempus. Donec vitae sapien ut libero venenatis faucibus. Nullam quis ante.</p>
    <p>Etiam rhoncus. Maecenas tempus, tellus eget condimentum rhoncus, sem quam semper libero, sit amet adipiscing sem neque sed ipsum. Nam quam nunc, blandit vel, luctus pulvinar, hendrerit id, lorem. Maecenas nec odio et ante tincidunt tempus. Donec vitae sapien ut libero venenatis faucibus. Nullam quis ante.</p>
    <p>Etiam rhoncus. Maecenas tempus, tellus eget condimentum rhoncus, sem quam semper libero,</p>
    <p class="letter-sign">Regards,<br>Ahmed Rahman.<br>02.02.2014</p>
  </div>
  <div class="letter-footer">
    <strong>Office</strong>
    <span>Room C, Unit 408, 4/F, Lok Tin Ind. Bldg,<br>No. 12 Hoi Yuen Road, Kwun Tong, Kowloon, HKSAR</span>
  </div>
  <svg class="band" viewBox="0 0 397 18" preserveAspectRatio="none" aria-hidden="true">
    <rect x="0" y="10" width="397" height="3" fill="#00a990"/>
    <rect x="0" y="13" width="397" height="5" fill="#0292cd"/>
    <path d="M250 10 L268 0 L397 0 L397 10 Z" fill="#0292cd"/>
  </svg>
</section>

<!-- presentation folder -->
<section class="piece folder" aria-label="Presentation folder">
  <div class="flap"></div>
  <div class="wordmark">RiverPine</div>
</section>

<!-- pens -->
<div class="pen pen-one" role="img" aria-label="Blue branded ballpoint pen"></div>
<div class="pen pen-two" role="img" aria-label="Blue branded ballpoint pen"></div>

<!-- envelope front -->
<section class="piece envelope-front" aria-label="Envelope front">
  <div class="wordmark">RiverPine</div>
  <div class="contacts">
    <ul class="contact-list">
      <li><svg viewBox="0 0 10 10"><path d="M2 1l2 2-1 1.5c.6 1.2 1.4 2 2.5 2.5L7 6l2 2-1.5 1.5C5 9 1 5 .5 2.5z" fill="#0292cd"/></svg>(852) 5512 0846</li>
      <li><svg viewBox="0 0 10 10"><rect x="0.5" y="2" width="9" height="6" fill="#0292cd"/><path d="M.5 2l4.5 3.5L9.5 2" stroke="#fff" fill="none" stroke-width=".8"/></svg>danielwong@hkriverpine.com.hk</li>
      <li class="web"><svg viewBox="0 0 10 10"><circle cx="5" cy="5" r="4.5" fill="#0292cd"/></svg>www.<b>hkriverpine</b>.com.hk</li>
    </ul>
  </div>
  <div class="divider"></div>
  <div class="address">Room C, Unit 408, 4/F, Lok Tin Ind. Bldg,<br>No. 12 Hoi Yuen Road, Kwun Tong,<br>Kowloon, HKSAR</div>
  <svg class="band" viewBox="0 0 417 16" preserveAspectRatio="none" aria-hidden="true">
    <rect x="0" y="8" width="417" height="2" fill="#00a990"/>
    <rect x="0" y="10" width="417" height="6" fill="#0292cd"/>
    <path d="M250 8 L264 0 L417 0 L417 8 Z" fill="#0292cd"/>
  </svg>
</section>

<!-- envelope back -->
<section class="piece envelope-back" aria-label="Envelope back">
  <svg class="fold" viewBox="0 0 414 207" preserveAspectRatio="none" aria-hidden="true">
    <path d="M0 0 L207 95 L414 0" fill="none" stroke="#dcdfe1" stroke-width="1.2"/>
  </svg>
  <div class="wordmark">RiverPine</div>
</section>

</body>
</html>
```